QP Fiduciary Website Redesign Contest

We want to refresh our website to be more insitutional, professional for an international audience. We have designed a new logo for this purpose and that has been attached. A full brand brief and positioning statement has also been attached. Please read through all the documents carefully before designing. The old website is found here: https://qp-fiduciary.example/

Target Market(s)

Actuaries and associated businesses internationally

Industry/Entity Type

professional services - actuaries

Number of Pages Required

3 page

Font styles to use
Sans Serif

Colors
0054AA
0677BA
7BADD7
CADEEF
E8F1F8
0094D4
00A9DD
6FCCEA
C7EBF8
E9F6FB
F0912C
F2A743
F7CA91
FBE8D2
FDF5EE
EE7325
F08F49
F5BC92
FAE3D3
FDF4ED
EB3D1F
EC4F4E
F09395
F8D3D4
FCEDEE

Requirements
Must have
• blues and greens to match the logo color, complimentary colors, navigation
Nice to have
• old site: https://qp-fiduciary.example/

```html
<!DOCTYPE html>
<html lang="en">
<head>
<meta charset="utf-8">
<title>QP Fiduciary — Actuarial Software</title>
<link href="https://fonts.googleapis.com/css2?family=Inter:wght@400;500;600;700&family=Michroma&family=Space+Mono&display=swap" rel="stylesheet">
<style>
:root{
  --accent:#0054AA;
  --accent-2:#0094D4;
  --accent-3:#00A9DD;
  --accent-soft:#E8F1F8;
  --accent-soft-2:#E9F6FB;
  --accent-line:#7BADD7;
  --accent-light:#6FCCEA;
  --warm:#F0912C;
  --ink:#12223A;
  --body:#4F5B6B;
  --muted:#8390A0;
  --line:#DDE8F2;
  --bg-soft:#F4F8FC;
  --bg-white:#FFFFFF;
  --dark:#0B1D33;
}
*{box-sizing:border-box;margin:0;padding:0}
html,body{width:1200px;height:4461px;overflow:hidden}
body{font-family:"Inter",Arial,sans-serif;color:var(--ink);background:var(--bg-white)}
a{color:inherit;text-decoration:none}
.btn{display:inline-flex;align-items:center;gap:8px;background:linear-gradient(90deg,var(--accent),var(--accent-2));color:#fff;font-weight:600;font-size:13px;border-radius:22px;padding:0 24px;height:38px;box-shadow:0 8px 20px rgba(0,84,170,.25)}
.btn svg{width:12px;height:12px}
.tag{display:inline-block;font-family:"Space Mono",monospace;font-size:9px;letter-spacing:1.5px;color:var(--accent);background:var(--accent-soft);border:1px solid var(--accent-line);border-radius:10px;padding:3px 10px;text-transform:uppercase}
.section{position:relative;width:1200px}
h2{font-size:38px;font-weight:600;letter-spacing:-1.2px;line-height:1.08}
.lead{font-size:13.5px;line-height:1.75;color:var(--body)}

/* nav */
.nav{height:64px;display:flex;align-items:center;padding:0 20px 0 72px;background:#fff;border-bottom:1px solid var(--line)}
.brand{display:flex;align-items:center;gap:10px;font-weight:600;font-size:24px;color:var(--accent);letter-spacing:.5px;text-transform:uppercase}
.brand i{width:12px;height:12px;border-radius:50%;background:var(--accent-3);display:block}
.nav-links{display:flex;gap:34px;margin-left:auto;margin-right:36px;font-size:13px;color:#2c3a4e}
.nav-links .active{color:var(--accent-2);font-weight:500}
.nav .btn{height:40px;font-size:13px;font-weight:500}

/* hero */
.hero{height:453px;background:linear-gradient(100deg,#081a33 0%,#0c2748 40%,#103866 65%,#0a4f8a 85%,#0677BA 100%);color:#fff;padding:46px 0 0 104px}
.hero .photo{position:absolute;inset:0}
.hero-in{position:relative}
.hero h1{font-size:56px;font-weight:600;letter-spacing:-2px;line-height:1.04;width:620px}
.hero p{margin-top:30px;font-size:15px;line-height:1.6;color:rgba(255,255,255,.82);width:480px}
.hero .btn{margin-top:30px}

/* overview */
.overview{height:751px;background:var(--bg-soft);padding:155px 0 0 104px}
.overview h2{margin-top:18px}
.overview .lead{margin-top:18px;width:500px}
.cards4{display:flex;gap:26px;margin-top:50px}
.fcard{width:228px;height:218px;background:#fff;border:1px solid var(--line);border-radius:12px;padding:28px 24px}
.icon{width:38px;height:38px;border-radius:9px;background:var(--accent-soft);display:flex;align-items:center;justify-content:center}
.icon svg{width:16px;height:16px;stroke:var(--accent);fill:none;stroke-width:1.8}
.fcard h3{font-size:14px;font-weight:600;margin-top:26px;line-height:1.4}
.fcard p{font-size:11px;line-height:1.7;color:var(--body);margin-top:12px}

/* solutions */
.solutions{height:742px;background:#fff}
.sol-text{position:absolute;left:104px;top:260px;width:380px}
.sol-text h2{margin-top:20px;font-size:39px}
.sol-text .lead{margin-top:22px;font-size:12.5px}
.sol-text .btn{margin-top:28px}
.scard{position:absolute;background:#fff;border:1px solid var(--line);border-radius:12px;overflow:hidden}
.scard .img{display:block;width:100%}
.scard h3{font-size:14px;font-weight:600;margin:22px 24px 0}
.scard p{font-size:11.5px;line-height:1.75;color:var(--body);margin:12px 24px 0}
.s1{left:533px;top:103px;width:564px;height:266px}
.s1 .img{height:155px;background:linear-gradient(180deg,#0a1a2e,#0f2a4a 60%,#0677BA)}
.s2{left:533px;top:390px;width:272px;height:272px}
.s2 .img{height:129px;background:linear-gradient(160deg,#0a1726,#12304f 70%,#0054AA)}
.s3{left:825px;top:390px;width:272px;height:272px}
.s3 .img{height:129px;background:radial-gradient(circle at 50% 45%,#00A9DD,#0054AA 50%,#071a33)}

/* characteristics */
.traits{height:770px;background:var(--bg-soft);text-align:center;padding-top:184px}
.traits h2{margin-top:20px}
.traits .lead{margin:16px auto 0;width:520px;font-size:12.5px}
.tgrid{position:absolute;left:258px;top:405px;display:grid;grid-template-columns:375px 320px;row-gap:70px;text-align:left}
.trait{display:flex;gap:20px}
.trait .icon{flex:none;width:44px;height:44px;background:var(--accent-soft-2)}
.trait .icon svg{stroke:var(--accent-2)}
.trait h3{font-size:14px;font-weight:600;margin-top:4px}
.trait p{font-size:11.5px;line-height:1.7;color:var(--body);margin-top:8px;width:260px}

/* insights */
.insights{height:852px;background:#fff;text-align:center;padding-top:118px}
.insights h2{margin-top:20px}
.insights .lead{margin:16px auto 0;width:520px;font-size:12.5px}
.acards{display:flex;gap:26px;margin:52px 0 0 104px;text-align:left}
.acard{width:314px;height:368px;border:1px solid var(--line);border-radius:12px;overflow:hidden;background:#fff}
.acard .img{height:195px}
.a1 .img{background:linear-gradient(135deg,#2f3f55,#9fb6cc 55%,#e6edf4)}
.a2 .img{background:linear-gradient(135deg,#0a1320,#13243c 60%,#0677BA)}
.a3 .img{background:linear-gradient(135deg,#2a2f3a,#5a6a7e 45%,#e6eaf0 70%,#8b98a8)}
.meta{display:flex;align-items:center;gap:6px;font-size:9.5px;color:var(--muted);margin:20px 20px 0}
.meta b{font-weight:500;color:var(--accent-2);margin-left:6px}
.meta svg{width:10px;height:10px;stroke:var(--muted);fill:none;stroke-width:1.6}
.acard h3{font-size:13.5px;font-weight:600;line-height:1.45;margin:14px 20px 0}
.acard p{font-size:10.5px;line-height:1.75;color:var(--body);margin:8px 20px 0}
.more{display:inline-block;font-size:10.5px;font-weight:600;color:var(--accent);margin:14px 20px 0}
.insights .view{margin-top:38px;background:var(--accent-line);box-shadow:none}

/* cta */
.cta{height:478px;background:linear-gradient(95deg,#07182c 0%,#0b2544 40%,#0e3560 65%,#0a2340 100%);color:#fff;padding:106px 0 0 104px}
.cta h2{color:#fff;margin-top:10px;width:460px}
.cta p{margin-top:24px;width:400px;font-size:13.5px;line-height:1.75;color:rgba(255,255,255,.78)}
.cta .btn{margin-top:30px}
.cta .tag{color:var(--accent-light);background:rgba(0,148,212,.18);border-color:rgba(111,204,234,.5)}

/* footer */
.footer{height:351px;background:var(--dark);color:#cfd8e3;padding:0 138px}
.fcol{position:absolute;top:58px}
.flogo{left:138px;top:52px;color:#fff;font-size:34px}
.fdesc{left:138px;top:122px;width:300px;font-size:11.5px;line-height:1.65;color:#b9c6d6}
.ftitle{font-family:"Michroma",sans-serif;font-size:14px;color:#fff;letter-spacing:.5px;padding-bottom:8px;border-bottom:1px solid var(--accent-3);display:inline-block;text-transform:uppercase}
.qlinks{left:558px}
.qlinks ul{list-style:none;margin-top:18px}
.qlinks li{font-size:11.5px;margin-bottom:12px}
.contact{left:788px}
.crow{display:flex;gap:14px;font-size:11.5px;line-height:1.65;margin-top:18px}
.crow svg{flex:none;width:14px;height:14px;fill:var(--accent-light);margin-top:2px}
.crow b{font-weight:600;color:#fff}
.fbottom{position:absolute;left:138px;right:172px;top:288px;border-top:1px solid #1e3553;padding-top:20px;display:flex;align-items:center;font-size:11px;color:#b9c6d6}
.fbottom .legal{margin-left:22px}
.social{margin-left:auto;display:flex;gap:10px}
.social span{width:28px;height:28px;border-radius:50%;border:1px solid #fff;display:block}
.social span:first-child{background:#fff}
</style>
</head>
<body>

<header class="nav">
  <a class="brand" href="https://qp-fiduciary.example/"><i></i>QP Fiduciary</a>
  <nav class="nav-links">
    <a class="active" href="#">Home</a><a href="#">Platform</a><a href="#">Solutions</a><a href="#">Insights</a><a href="#">Company</a><a href="#">Contact</a>
  </nav>
  <a class="btn" href="#">Request a Technical Walkthrough</a>
</header>

<section class="section hero">
  <div class="photo" role="img" aria-label="Analyst at a desk in front of monitors showing financial bar charts"></div>
  <div class="hero-in">
    <h1>Actuarial Software For Structured, Auditable Financial Analysis.</h1>
    <p>QP Fiduciary develops software that transforms established actuarial methodologies into compliant, decision-ready tools.</p>
    <a class="btn" href="#">Request a Technical Walkthrough <svg viewBox="0 0 12 12" fill="none" stroke="#fff" stroke-width="1.6"><path d="M2 6h8M7 3l3 3-3 3"/></svg></a>
  </div>
</section>

<section class="section overview">
  <span class="tag">Platform Overview</span>
  <h2>Built For Actuarial Excellence</h2>
  <p class="lead">Our platform delivers structured workflows, transparent assumptions, and complete auditability — enabling confident, governance-ready financial analysis.</p>
  <div class="cards4">
    <div class="fcard"><div class="icon"><svg viewBox="0 0 16 16"><circle cx="4" cy="12" r="2"/><circle cx="12" cy="4" r="2"/><path d="M4 10V6a2 2 0 0 1 2-2h4"/></svg></div><h3>Structured Workflows</h3><p>Compliance processes that guide analysts from input to output with clear and deterministic steps.</p></div>
    <div class="fcard"><div class="icon"><svg viewBox="0 0 16 16"><path d="M1 8s3-5 7-5 7 5 7 5-3 5-7 5-7-5-7-5z"/><circle cx="8" cy="8" r="2"/></svg></div><h3>Transparency of Assumptions</h3><p>Track assumptions at every junction, documented, traced, and reviewable throughout.</p></div>
    <div class="fcard"><div class="icon"><svg viewBox="0 0 16 16"><path d="M8 1l6 2.5v4c0 3.5-2.6 6-6 7.5-3.4-1.5-6-4-6-7.5v-4z"/></svg></div><h3>Auditability</h3><p>Complete audit trails with version control. Designed for auditors, built for compliance.</p></div>
    <div class="fcard"><div class="icon"><svg viewBox="0 0 16 16"><path d="M8 2v12M3 14h10M3 5h10M3 5l-2 5h4zM13 5l-2 5h4z"/></svg></div><h3>Governance</h3><p>Built-in controls to support role-based access and regulatory compliance frameworks.</p></div>
  </div>
</section>

<section class="section solutions">
  <div class="sol-text">
    <span class="tag">Our Solutions</span>
    <h2>Comprehensive Actuarial Suite</h2>
    <p class="lead">Three integrated solution areas designed to address the full spectrum of actuarial analysis needs.</p>
    <a class="btn" href="#">Request a Technical Walkthrough <svg viewBox="0 0 12 12" fill="none" stroke="#fff" stroke-width="1.6"><path d="M2 6h8M7 3l3 3-3 3"/></svg></a>
  </div>
  <article class="scard s1"><div class="img" role="img" aria-label="Dark analytics dashboard with bar and line charts"></div><h3>Reserving &amp; Valuation</h3><p>Comprehensive reserve calculations and liability valuations with transparent methodology. Actuarial-first design with full audit support.</p></article>
  <article class="scard s2"><div class="img" role="img" aria-label="Pricing analysis software screen with charts and tables"></div><h3>Pricing</h3><p>Sophisticated pricing models that produce reliable results with competitive benchmarking and regulatory-ready outputs.</p></article>
  <article class="scard s3"><div class="img" role="img" aria-label="Glowing shield illustration representing risk"></div><h3>Enterprise Risk Management</h3><p>Holistic risk assessment and capital modelling that integrates across lines of business and regulatory frameworks.</p></article>
</section>

<section class="section traits">
  <span class="tag">Why Choose Us</span>
  <h2>Platform Characteristics</h2>
  <p class="lead">Key attributes that set our platform apart in delivering reliable, governance-ready actuarial analysis.</p>
  <div class="tgrid">
    <div class="trait"><div class="icon"><svg viewBox="0 0 16 16"><circle cx="4" cy="4" r="2"/><circle cx="12" cy="12" r="2"/><path d="M4 6v2a2 2 0 0 0 2 2h4"/></svg></div><div><h3>Structured Workflows</h3><p>Guided step-by-step processes ensuring consistency and compliance.</p></div></div>
    <div class="trait"><div class="icon"><svg viewBox="0 0 16 16"><path d="M2 2v12h12M4 11l3-4 3 2 4-5"/></svg></div><div><h3>Comparative Analysis Capability</h3><p>Side-by-side scenario evaluation with built-in sensitivity testing.</p></div></div>
    <div class="trait"><div class="icon"><svg viewBox="0 0 16 16"><circle cx="8" cy="8" r="6.5"/><path d="M1.5 8h13M8 1.5c2 2 2 11 0 13M8 1.5c-2 2-2 11 0 13"/></svg></div><div><h3>Multi-Jurisdictional Review Support</h3><p>Supports reporting across multiple regulatory environments.</p></div></div>
    <div class="trait"><div class="icon"><svg viewBox="0 0 16 16"><path d="M5 10a5 5 0 1 1 6 0v2H5zM6 14h4"/></svg></div><div><h3>Transparent Assumptions</h3><p>Every assumption documented, traceable, and ready for review.</p></div></div>
  </div>
</section>

<section class="section insights">
  <span class="tag">Insights</span>
  <h2>Insights &amp; Thought Leadership</h2>
  <p class="lead">Key publications that set our platform apart in delivering reliable, governance-ready actuarial analysis.</p>
  <div class="acards">
    <article class="acard a1"><div class="img" role="img" aria-label="Printed financial report with pie and bar charts on a desk"></div>
      <div class="meta"><svg viewBox="0 0 10 10"><rect x="1" y="2" width="8" height="7"/><path d="M1 4h8"/></svg>24 Jul 2025<b>Governance</b></div>
      <h3>RBC (Risk-Based Capital)</h3><p>Harbor Point, 24 July 2025 — QP Fiduciary, an independent actuarial consulting firm...</p><a class="more" href="#">Read More →</a></article>
    <article class="acard a2"><div class="img" role="img" aria-label="Dark analytics dashboard on a screen"></div>
      <div class="meta"><svg viewBox="0 0 10 10"><rect x="1" y="2" width="8" height="7"/><path d="M1 4h8"/></svg>15 Jan 2026<b>Technology</b></div>
      <h3>Evolution Into Technology-Led Actuarial Platforms</h3><p>Harbor Point, January 12, 2026 — QP Fiduciary is rethinking the actuarial workflow...</p><a class="more" href="#">Read More →</a></article>
    <article class="acard a3"><div class="img" role="img" aria-label="Printed standards document lying on a wooden table"></div>
      <div class="meta"><svg viewBox="0 0 10 10"><rect x="1" y="2" width="8" height="7"/><path d="M1 4h8"/></svg>17 Jan 2026<b>Governance</b></div>
      <h3>IFRS 17: A Paradigm Shift For Financial Reporting</h3><p>Harbor Point, January 17, 2026 — QP Fiduciary is an actuarial consulting firm leading...</p><a class="more" href="#">Read More →</a></article>
  </div>
  <a class="btn view" href="#">View All Articles <svg viewBox="0 0 12 12" fill="none" stroke="#fff" stroke-width="1.6"><path d="M2 6h8M7 3l3 3-3 3"/></svg></a>
</section>

<section class="section cta" role="img" aria-label="Professional working on a laptop in a dim office">
  <span class="tag">Schedule a Demo</span>
  <h2>Ready To Transform Your Actuarial Practice?</h2>
  <p>Discover how QP Fiduciary's platform can bring structure, transparency, and confidence to your financial analysis workflows.</p>
  <a class="btn" href="#">Request a Technical Walkthrough <svg viewBox="0 0 12 12" fill="none" stroke="#fff" stroke-width="1.6"><path d="M2 6h8M7 3l3 3-3 3"/></svg></a>
</section>

<footer class="section footer">
  <a class="brand fcol flogo" href="https://qp-fiduciary.example/"><i></i>QP Fiduciary</a>
  <p class="fcol fdesc">Software that translates actuarial methodologies into disciplined decision-ready analytical tools across diverse regulatory environments.</p>
  <div class="fcol qlinks"><span class="ftitle">Quick Links</span>
    <ul><li>Home</li><li>Platform</li><li>Solutions</li><li>Insights</li><li>Company</li><li>Contact</li></ul></div>
  <div class="fcol contact"><span class="ftitle">Contact Details</span>
    <div class="crow"><svg viewBox="0 0 14 14"><path d="M7 0a5 5 0 0 1 5 5c0 4-5 9-5 9S2 9 2 5a5 5 0 0 1 5-5zm0 3a2 2 0 1 0 0 4 2 2 0 0 0 0-4z"/></svg><div><b>QP Fiduciary, Inc.</b><br>480 Meridian Row, Suite 210<br>Harbor Point, FL 30990</div></div>
    <div class="crow"><svg viewBox="0 0 14 14"><path d="M3 1l2.5 3-1.5 1.5a8 8 0 0 0 4.5 4.5L10 8.5l3 2.5-1.5 2.5C6 13 1 8 .5 2.5z"/></svg><div><b>+1(555)013-4820</b></div></div>
    <div class="crow"><svg viewBox="0 0 14 14"><path d="M1 3h12v8H1zM1 3l6 4.5L13 3" stroke="#0B1D33" stroke-width="1"/></svg><div>hello@qp-fiduciary.example</div></div>
  </div>
  <div class="fbottom"><span>© 2026 QP Fiduciary. All rights reserved.</span><span class="legal">Privacy · Terms</span>
    <div class="social" aria-label="Social links"><span></span><span></span><span></span></div></div>
</footer>

</body>
</html>
```